Business Card for Beach theme sports bar called MORVIN

I need a business card designed for our employees, front and back. This will be used by the employees of two business locations to hand out to customers. I've attached the previous business cards we used at one time for a Dantells (it is now Morvin). Looking for a fresh new card that is elegant but has character.

Target Market(s)

30-60, middle class

Contact Information for Business Card

We are a beach bar and sports bar. I am looking for an elegant business card with the front to have the MORVIN logo. Then on the back I need it to allow a space for employees to write their names and for them to write in their schedule. I have attached our old cards with our old name Dantells so you can pull everything we need on the cards. one thing is missing is we have another location at 2615 W Calder Ridge Rd with a number of 702-418-9053. Since we will use it for both locations it should allow the employee to circle or check mark the bar which they work at.

Font styles to use
Sans Serif

Requirements
Must have
• We are looking for some fresh ideas for the business card. Something that will really stick out to customers when the staff hands them out. Creativity will be looked at positively, but we still want it to look upscale and fun.

```html
<!DOCTYPE html>
<html lang="en">
<head>
<meta charset="utf-8">
<title>MORVIN Business Card</title>
<link rel="stylesheet" href="https://fonts.googleapis.com/css2?family=Montserrat:wght@800&family=Open+Sans:wght@400;600;700&display=swap">
<style>
  :root {
    --stage: #3b3b3d;
    --ink: #0d0d0d;
    --paper: #ffffff;
    --muted: #d9d9d9;
    --rule: #8a8a8a;
  }
  * { margin: 0; padding: 0; box-sizing: border-box; }
  html, body { width: 1200px; height: 1200px; overflow: hidden; }
  body {
    background: radial-gradient(circle at 50% 40%, #4a4a4c 0%, var(--stage) 70%);
    font-family: "Open Sans", sans-serif;
    position: relative;
  }
  .card {
    position: absolute;
    left: 250px;
    width: 700px;
    height: 400px;
    border-radius: 4px;
    overflow: hidden;
    box-shadow: 0 18px 40px rgba(0,0,0,.45);
  }
  .card--back { top: 120px; background: var(--paper); }
  .card--front { top: 660px; background: var(--ink); }

  .back-field { position: absolute; inset: 0; }

  .contact {
    position: absolute;
    left: 36px;
    top: 28px;
    width: 340px;
    color: var(--paper);
  }
  .contact__name {
    font-weight: 700;
    font-size: 24px;
    line-height: 1.2;
  }
  .contact__title {
    font-size: 15px;
    color: var(--muted);
    margin-top: 2px;
  }
  .write-field {
    display: flex;
    align-items: flex-end;
    gap: 10px;
    font-size: 13px;
    color: var(--muted);
    margin-top: 10px;
    height: 22px;
  }
  .write-field__line {
    flex: 1;
    border-bottom: 1px solid var(--rule);
    height: 100%;
  }
  .write-field--name { margin-top: 6px; }
  .write-field__label { width: 64px; flex: none; }

  .contact__rows { margin-top: 14px; }
  .contact__row {
    display: flex;
    align-items: center;
    gap: 10px;
    font-size: 14px;
    line-height: 1.65;
    color: var(--muted);
  }
  .contact__icon { width: 14px; height: 14px; flex: none; }

  .locations { margin-top: 12px; }
  .location {
    display: flex;
    align-items: flex-start;
    gap: 10px;
    font-size: 14px;
    line-height: 1.4;
    color: var(--muted);
    margin-top: 6px;
  }
  .location__box {
    width: 14px;
    height: 14px;
    flex: none;
    margin-top: 3px;
    border: 1.5px solid var(--paper);
  }

  .brand {
    position: absolute;
    display: flex;
    align-items: center;
    gap: 14px;
    font-family: "Montserrat", sans-serif;
    font-weight: 800;
    letter-spacing: 4px;
  }
  .brand__dot { width: 18px; height: 18px; border-radius: 50%; flex: none; }
  .brand--back { right: 36px; bottom: 36px; font-size: 40px; color: var(--ink); }
  .brand--back .brand__dot { background: var(--ink); }
  .brand--front { left: 50%; top: 50%; transform: translate(-50%, -50%); font-size: 64px; color: var(--paper); }
  .brand--front .brand__dot { width: 22px; height: 22px; background: var(--paper); }
</style>
</head>
<body>

<section class="card card--back" aria-label="Card back with staff contact details">
  <svg class="back-field" viewBox="0 0 700 400" width="700" height="400" aria-hidden="true">
    <path d="M0 0 H530 C480 100 550 200 480 260 C420 310 370 330 350 400 H0 Z" fill="var(--ink)"/>
    <path d="M530 0 C480 100 550 200 480 260 C420 310 370 330 350 400" fill="none" stroke="var(--ink)" stroke-width="3" stroke-dasharray="2 4" transform="translate(8 6)"/>
  </svg>

  <div class="contact">
    <p class="contact__name">Your Name</p>
    <div class="write-field write-field--name"><span class="write-field__label">Name</span><span class="write-field__line"></span></div>
    <p class="contact__title">Your Title</p>
    <div class="write-field"><span class="write-field__label">Schedule</span><span class="write-field__line"></span></div>

    <div class="contact__rows">
      <p class="contact__row">
        <svg class="contact__icon" viewBox="0 0 16 16"><rect x="1" y="3" width="14" height="10" fill="none" stroke="currentColor" stroke-width="1.5"/><path d="M1 3 L8 9 L15 3" fill="none" stroke="currentColor" stroke-width="1.5"/></svg>
        youremail@morvinbar.com
      </p>
      <p class="contact__row">
        <svg class="contact__icon" viewBox="0 0 16 16"><circle cx="8" cy="8" r="6.5" fill="none" stroke="currentColor" stroke-width="1.5"/><path d="M1.5 8 H14.5 M8 1.5 C5 5 5 11 8 14.5 M8 1.5 C11 5 11 11 8 14.5" fill="none" stroke="currentColor" stroke-width="1.2"/></svg>
        www.morvinbar.com
      </p>
    </div>

    <div class="locations">
      <p class="location"><span class="location__box"></span><span>2615 W Calder Ridge Rd · 702-418-9053</span></p>
      <p class="location"><span class="location__box"></span><span>1180 E Harlow Bay Dr · 702-555-0147</span></p>
    </div>
  </div>

  <div class="brand brand--back">
    <span class="brand__dot"></span>
    <span class="brand__name">MORVIN</span>
  </div>
</section>

<section class="card card--front" aria-label="Card front with brand name">
  <div class="brand brand--front">
    <span class="brand__dot"></span>
    <span class="brand__name">MORVIN</span>
  </div>
</section>

</body>
</html>
```